Website Design for a different kind of Business Consulting organisation needed!

We need a website design that reflects who we are, the simplicity of our consulting business and with a focus on our priority - to help our clients deliver, or execute - the "e" in Vantor-i.

Our key high level requirements are:
1) Simple and intuitive look and feel
2) Integration with all key social media platforms, twitter, facebook, linkedin, tumblr.

10 pages, tops.
- Main page - Welcome
- About Us/ Who are Vantor-i?
- 5 services pages - Project Management, Business Process Management, Change Management, Business Analysis and Finance Systems
- Contact Us

Something like:
http://www.lumvexhold.example/

Vantor-i is a registered trademark and all Logos and other branded material are attached for reference.

So, what’s our gig: A few snippets from previous work...

We are a different kind of business consulting group. We partner with our clients to help them deliver change. We don't just provide them with the theory. We also provide them with the leadership and capability to execute the change.

We aren’t a one stop shop, and we don’t offer cookie cutter solutions. We’re a boutique consulting firm covering Project Management, Business Process Management, Change Management and Business Analytics.

Vantor-i is a professional services organisation that partners with their clients to lead the execution of strategic process and system improvement initiatives. Vantor-i combines hands on delivery with coaching in best practice methodologies and approaches to build their clients capabilities to ensure their ongoing success in project implementations.

UPDATES:

Thanks to everyone who has submitted designs so far. The standard of designs coming through is quite high, with lots of professional designs that nail the design brief. Eliminating them is proving to be quite challenging.

A few updates to the job brief:
- Please make sure the design fits on one page. We would like all of our information to be on the first page that people see without them having to scroll down
- Please ensure you include the FIVE services we offer in the design
- Please use corporate images/istock photos in your designs which are relevant to our business
- Please add a section for a live twitter feed from our twitter account and a link to google+
- Please add a section for news/updates

Also, if you are able to build a site once a design is selected, please let us know.

Thanks,

Maribel.

Target Market(s)

Our target customers are large enterprises in Australia that are growing rapidly and have recently (last 24 months) undertaken or are currently undergoing software implementations and business process improvement programs. These businesses have a turnover of $100m or above and are working hard to differentiate themselves from their competitors but are not seeing the return on investment promised by software vendors and process improvement initiatives.

Industry/Entity Type

Leadership

Requirements
Must have
• Collaboration / Training / Workshop / Consulting images all of a professional nature.
Simple, non-cluttered look with plenty of white space.

```html
<!DOCTYPE html>
<html lang="en">
<head>
<meta charset="utf-8">
<title>Vantor-i | About</title>
<link rel="stylesheet" href="https://fonts.googleapis.com/css2?family=Open+Sans:wght@400;600;700&display=swap">
<style>
:root{
  --brand:#0a56a8;
  --brand-dark:#0b4f9c;
  --text:#3a3a3a;
  --muted:#8a8a8a;
  --nav:#7a7a7a;
  --rule:#dcdcdc;
  --icon-grey:#6e6e6e;
  --white:#ffffff;
}
*{margin:0;padding:0;box-sizing:border-box}
html,body{width:861px;height:1200px;overflow:hidden;background:var(--white)}
body{position:relative;font-family:"Open Sans",Arial,sans-serif;color:var(--text)}
.top-band{position:absolute;left:0;top:0;width:861px;height:5px;background:var(--brand)}
.brand{position:absolute;left:86px;top:20px;display:flex;align-items:center;gap:6px;color:var(--brand);font-size:34px;font-weight:400;letter-spacing:.5px;line-height:1}
.brand-dot{width:12px;height:12px;border-radius:50%;background:var(--brand)}
.header-social{position:absolute;left:660px;top:12px;display:flex;gap:6px}
.header-social span{width:24px;height:24px;border-radius:50%;background:var(--icon-grey)}
.header-social span.accent{background:var(--brand)}
.main-nav{position:absolute;top:52px;left:360px;display:flex;font-size:12px;font-weight:600;text-transform:uppercase}
.main-nav a{color:var(--nav);text-decoration:none;height:16px;line-height:16px;padding:0 11px;margin-right:16px}
.main-nav a.active{background:var(--brand);color:var(--white);padding:0 11px}
.rule{position:absolute;left:86px;width:688px;height:1px;background:var(--rule)}
.intro{position:absolute;left:86px;top:96px;width:690px}
.intro h1{color:var(--brand);font-size:22px;font-weight:700;line-height:30px;margin-bottom:8px}
.intro p,.member-bio p{font-size:12.2px;line-height:18px;margin-bottom:10px}
.member{position:absolute;left:86px;width:690px;height:200px}
.member-photo{position:absolute;left:0;top:0;width:168px;height:168px;border-radius:50%}
.p1{background:radial-gradient(circle at 45% 40%,#c9b7a4,#8fa3b4 60%,#dfe5ea)}
.p2{background:radial-gradient(circle at 50% 40%,#b9a08c,#9fb1c8 55%,#e3e8ee)}
.p3{background:radial-gradient(circle at 50% 45%,#a88a70,#7b6a5c 55%,#d9d3cb)}
.member-head{position:absolute;left:195px;top:0;width:495px}
.member-name{color:var(--brand);font-size:17.5px;font-weight:700;line-height:24px}
.member-role{color:var(--muted);font-size:12px;line-height:18px}
.follow{position:absolute;right:0;top:0;width:76px;font-size:11px;color:var(--brand);line-height:16px}
.follow-icons{display:flex;gap:8px;margin-top:4px}
.follow-icons span{width:16px;height:16px;border-radius:50%;background:var(--icon-grey)}
.member-bio{position:absolute;left:195px;top:50px;width:496px}
.site-footer{position:absolute;left:0;top:1112px;width:861px;height:88px;background:var(--brand-dark);color:var(--white)}
.footer-col{position:absolute;top:18px;font-size:8.4px;line-height:14px}
.footer-col h4{font-size:10px;font-weight:700;text-transform:uppercase;line-height:14px;margin-bottom:0}
.footer-social{display:flex;gap:8px;margin-top:6px}
.footer-social span{width:22px;height:22px;border-radius:50%;background:var(--white)}
.page-links{display:grid;grid-template-columns:53px auto}
.footer-brand{position:absolute;left:609px;top:14px;display:flex;align-items:center;gap:5px;font-size:28px;line-height:1;font-weight:400}
.footer-brand .brand-dot{background:var(--white);width:10px;height:10px}
.copyright{position:absolute;left:609px;top:53px;font-size:8.4px}
</style>
</head>
<body>
<div class="top-band"></div>

<header>
  <div class="brand">Vantor-i<span class="brand-dot"></span></div>
  <div class="header-social" aria-label="Social links"><span></span><span class="accent"></span><span></span><span></span></div>
  <nav class="main-nav">
    <a href="#">Home</a><a href="#" class="active">About</a><a href="#">Services</a><a href="#">Partners</a><a href="#">Contact</a>
  </nav>
</header>
<div class="rule" style="top:82px"></div>

<section class="intro">
  <h1>About</h1>
  <p>Sed ut perspiciatis unde omnis iste natus error sit voluptatem accusantium doloremque laudantium, totam rem aperiam, eaque ipsa quae ab illo inventore veritatis et quasi architecto beatae vitae dicta sunt explicabo. Sed ut perspiciatis unde omnis iste natus error sit voluptatem accusantium doloremque laudantium, totam rem aperiam, eaque ipsa quae ab illo inventore veritatis et quasi architecto beatae vitae dicta sunt explicabo.</p>
  <p>Ut enim ad minima veniam, quis nostrum exercitationem ullam corporis suscipit laboriosam, nisi ut aliquid ex ea commodi consequatur? Quis autem vel eum iure reprehenderit qui in ea voluptate velit esse quam nihil molestiae consequatur, vel illum qui dolorem eum fugiat quo voluptas nulla pariatu</p>
</section>
<div class="rule" style="top:307px"></div>

<article class="member" style="top:364px">
  <div class="member-photo p1" role="img" aria-label="Portrait photo of a smiling consultant at a laptop"></div>
  <div class="member-head">
    <div class="member-name">Daniel Mercer Hale</div>
    <div class="member-role">Founder &amp; CEO</div>
    <div class="follow">follow me:<div class="follow-icons"><span></span><span></span><span></span></div></div>
  </div>
  <div class="member-bio">
    <p>Sed ut perspiciatis unde omnis iste natus error sit voluptatem accusantium doloremque laudantium, totam rem aperiam, eaque ipsa quae ab illo inventore veritatis et quasi architecto beatae vitae dicta sunt explicabo. Sed ut perspiciatis unde omnis iste natus error sit voluptatem accusantium doloremque laudantium, totam rem aperiam, eaque ipsa quae ab illo inventore veritatis et quasi architecto beatae vitae dicta sunt explicabo.</p>
    <p>Ut enim ad minima veniam, quis nostrum exercitationem ullam corporis suscipit laboriosam, nisi ut aliquid ex ea commodi consequatur? Quis autem vel eum iure reprehenderit qui in ea voluptate velit esse quam nihil molestiae consequatur, vel illum qui dolorem eum fugiat quo voluptas nulla pariatur.</p>
  </div>
</article>

<article class="member" style="top:624px">
  <div class="member-photo p2" role="img" aria-label="Portrait photo of a consultant in glasses in an office"></div>
  <div class="member-head">
    <div class="member-name">Owen Castellane</div>
    <div class="member-role">Founder &amp; CEO</div>
    <div class="follow">follow me:<div class="follow-icons"><span></span><span></span></div></div>
  </div>
  <div class="member-bio">
    <p>Sed ut perspiciatis unde omnis iste natus error sit voluptatem accusantium doloremque laudantium, totam rem aperiam, eaque ipsa quae ab illo inventore veritatis et quasi architecto beatae vitae dicta sunt explicabo.</p>
    <p>Sed ut perspiciatis unde omnis iste natus error sit voluptatem accusantium doloremque laudantium, totam rem aperiam, eaque ipsa quae ab illo inventore veritatis et quasi architecto beatae vitae dicta sunt explicabo.</p>
  </div>
</article>

<article class="member" style="top:863px">
  <div class="member-photo p3" role="img" aria-label="Portrait photo of a consultant at a laptop by a brick wall"></div>
  <div class="member-head">
    <div class="member-name">Felix Harrow</div>
    <div class="member-role">Founder &amp; CEO</div>
    <div class="follow">follow me:<div class="follow-icons"><span></span><span></span><span></span></div></div>
  </div>
  <div class="member-bio">
    <p>Sed ut perspiciatis unde omnis iste natus error sit voluptatem accusantium doloremque laudantium, totam rem aperiam, eaque ipsa quae ab illo inventore veritatis et quasi architecto beatae vitae dicta sunt explicabo.</p>
    <p>Sed ut perspiciatis unde omnis iste natus error sit voluptatem accusantium doloremque laudantium, totam rem aperiam, eaque ipsa quae ab illo inventore veritatis et quasi architecto beatae vitae dicta sunt explicabo.</p>
  </div>
</article>

<footer class="site-footer">
  <div class="footer-col" style="left:74px">
    <h4>Connect with us</h4>
    <div>on social media network</div>
    <div class="footer-social"><span></span><span></span><span></span><span></span></div>
  </div>
  <div class="footer-col" style="left:225px">
    <h4>Pages</h4>
    <div class="page-links">
      <span>Home</span><span>Term &amp; Conditions</span>
      <span>About</span><span>FAQ</span>
      <span>Services</span><span>Partners</span>
    </div>
  </div>
  <div class="footer-col" style="left:395px">
    <h4>Contact details</h4>
    <div>p: +61 3 400 118 205 &nbsp;f: +61 3 9000 4471</div>
    <div>Level 8, 22 Harbour Rd. Melbourne,</div>
    <div>Australia, 3000</div>
  </div>
  <div class="footer-brand">Vantor-i<span class="brand-dot"></span></div>
  <div class="copyright">Copyright © 2014 All Rights Reserved</div>
</footer>
</body>
</html>
```